Dovecote Realty

Business cards for 4 people

They need to say for all
87 Tarrow Quay, Boston MA 02114

Each person will have their own personal information
We would like gold embossing for the name of the company
Marla is the blonde sitting in the chair smiling her information should be on the back of the card with her name and information
Should say for slogan classic pattern, elevated experience
marla@dovecoteprops.com
(413) 555-0182

Odette is the brunette with wavy hair in the tan suit celina@dovecoteprops.com
(617) 555-0137

faith@dovecoteprops.com
(413) 555-0164
standing next to the chair

hope@dovecoteprops.com
(413) 555-0199
close up headshot

```html
<!DOCTYPE html>
<html lang="en">
<head>
<meta charset="utf-8">
<title>Dovecote Realty – Business Cards</title>
<link href="https://fonts.googleapis.com/css2?family=Montserrat:wght@400;500;600;700&display=swap" rel="stylesheet">
<style>
  :root {
    --navy: #243551;
    --gold: #e8b65a;
    --gold-soft: #d9b372;
    --band: #fbbd4e;
    --paper: #ffffff;
    --ink: #1d1d1f;
    --backdrop: #e4e2e4;
    --grey-text: #6b6b6b;
  }
  * { margin: 0; padding: 0; box-sizing: border-box; }
  html, body { width: 1200px; height: 1108px; overflow: hidden; }
  body {
    background: var(--backdrop);
    font-family: "Montserrat", sans-serif;
    position: relative;
  }
  .card {
    position: absolute;
    left: 205px;
    width: 793px;
    height: 449px;
    border-radius: 28px;
    overflow: hidden;
  }
  .card--front { top: 75px; background: var(--navy); }
  .card--back { top: 594px; background: var(--paper); }

  /* Front */
  .front-mark {
    position: absolute;
    left: 315px; top: 85px;
    width: 161px; height: 161px;
    border: 4px solid var(--gold);
    border-radius: 50%;
  }
  .brand-name {
    position: absolute;
    left: 0; width: 100%;
    text-align: center;
    color: var(--gold);
    font-weight: 500;
    line-height: 1;
    white-space: nowrap;
  }
  .front-name { top: 253px; font-size: 60px; letter-spacing: 3px; }
  .front-sub { top: 321px; font-size: 24px; letter-spacing: 22px; padding-left: 22px; }
  .front-web {
    position: absolute;
    left: 0; width: 100%; top: 397px;
    text-align: center;
    color: #fff;
    font-size: 17px;
  }
  .front-web strong { color: var(--gold); font-weight: 700; }

  /* Back */
  .portrait {
    position: absolute;
    left: 0; top: 46px;
    width: 232px; height: 310px;
    background: linear-gradient(180deg, #c9a488 0%, #8d5e3d 55%, #7a4f33 100%);
    border-radius: 0 40px 0 0;
  }
  .name-band {
    position: absolute;
    left: 0; top: 352px;
    width: 430px; height: 62px;
  }
  .agent-name {
    position: absolute;
    left: 41px; top: 357px;
    font-size: 28px; font-weight: 600; line-height: 1.1;
    color: #fff; letter-spacing: 0.5px;
  }
  .agent-role {
    position: absolute;
    left: 42px; top: 389px;
    font-size: 17.5px; line-height: 1.1; color: #fff;
  }
  .back-mark {
    position: absolute;
    left: 513px; top: 62px;
    width: 100px; height: 100px;
    border: 3px solid var(--gold-soft);
    border-radius: 50%;
  }
  .back-name { left: 313px; width: 500px; }
  .back-name.main { top: 161px; font-size: 38px; letter-spacing: 1.5px; color: var(--gold-soft); }
  .back-name.sub { top: 202px; font-size: 15px; letter-spacing: 13px; padding-left: 13px; color: var(--grey-text); }
  .contact-list {
    position: absolute;
    left: 421px; top: 302px;
    list-style: none;
  }
  .contact-list li {
    display: flex; align-items: center;
    height: 22.5px;
    font-size: 17px; color: var(--ink);
  }
  .contact-list svg { width: 17px; height: 14px; margin-right: 15px; flex: none; }
  .address-bar {
    position: absolute;
    left: 0; bottom: 0;
    width: 100%; height: 35px;
    background: var(--navy);
    color: var(--gold);
    font-size: 17.5px;
    text-align: center;
    line-height: 35px;
  }
</style>
</head>
<body>

<section class="card card--front">
  <div class="front-mark"></div>
  <div class="brand-name front-name">DOVECOTE</div>
  <div class="brand-name front-sub">REALTY</div>
  <div class="front-web">www.<strong>dovecoteprops</strong>.com</div>
</section>

<section class="card card--back">
  <div class="portrait" role="img" aria-label="Portrait photo of the agent in a tan blazer"></div>
  <svg class="name-band" viewBox="0 0 430 62" aria-hidden="true">
    <polygon points="0,0 377,0 430,62 0,62" fill="var(--band)"/>
  </svg>
  <div class="agent-name">MARLA VANCE</div>
  <div class="agent-role">Real Estate Agent</div>

  <div class="back-mark"></div>
  <div class="brand-name back-name main">DOVECOTE</div>
  <div class="brand-name back-name sub">REALTY</div>

  <ul class="contact-list">
    <li>
      <svg viewBox="0 0 17 14" aria-hidden="true"><path d="M1 5 Q8.5 -1 16 5 L14 7 L12 5 L12 3 Q8.5 2 5 3 L5 5 L3 7 Z M4 8 L13 8 L15 13 L2 13 Z" fill="var(--gold)"/></svg>
      (413) 555-0182
    </li>
    <li>
      <svg viewBox="0 0 17 14" aria-hidden="true"><rect x="1" y="2" width="15" height="10" fill="var(--gold)"/><path d="M1 2 L8.5 8 L16 2" stroke="#fff" stroke-width="1.3" fill="none"/></svg>
      marla@dovecoteprops.com
    </li>
    <li>
      <svg viewBox="0 0 17 14" aria-hidden="true"><circle cx="8.5" cy="7" r="6.3" fill="var(--gold)"/><path d="M2.5 7 H14.5 M8.5 0.7 V13.3" stroke="#fff" stroke-width="1"/></svg>
      www.dovecoteprops.com
    </li>
  </ul>

  <div class="address-bar">87 Tarrow Quay, Boston MA 02114</div>
</section>

</body>
</html>
```